Meridale Bed Company Needs Business Card

Looking for a very nice looking business card. Creative but not extravagant. We sell beds and pillows across the U.S. and need something professional but catchy. I have attached the logo.

Name : Devin Holt
Title : President
Phone : (800) 471-2960
Email: sleep@quilmora.com
Website: www.quilmora.com

Can be single-sided or double-sided
horizontal or vertical

Can use Blues/Greys

Target Market(s)

Mass Market

Industry/Entity Type

Retail

Contact Information for Business Card

Name : Devin Holt
Title : President
Phone : (800) 471-2960
Email: sleep@quilmora.com
Website: www.quilmora.com

Requirements
Must have
• Clean, Modern, Smooth
• Can use Blues/Greys
• On the other side without the information - have something simple like www.quilmora.com or our logo
Nice to have
• Surprise me
Should not have
• Nothing crazy, nothing cluttered

```html
<!DOCTYPE html>
<html lang="en">
<head>
<meta charset="utf-8">
<title>Quilmora Business Card</title>
<link rel="stylesheet" href="https://fonts.googleapis.com/css2?family=Open+Sans:wght@300;400;700&display=swap">
<style>
  :root {
    --backdrop: #e4e6e8;
    --brand-blue: #2ea3db;
    --brand-blue-deep: #1d86c2;
    --brand-blue-light: #4bb3e3;
    --brand-blue-mist: #d3ecf8;
    --ink-grey: #4a4f54;
    --card-white: #ffffff;
  }
  * { margin: 0; padding: 0; box-sizing: border-box; }
  html, body {
    width: 1200px;
    height: 843px;
    overflow: hidden;
    background: var(--backdrop);
    font-family: "Open Sans", Arial, sans-serif;
  }
  .sheet {
    position: relative;
    width: 1200px;
    height: 843px;
    display: flex;
    align-items: center;
    justify-content: center;
    gap: 40px;
  }
  .card {
    position: relative;
    width: 540px;
    height: 309px;
    overflow: hidden;
    box-shadow: 0 10px 28px rgba(0, 0, 0, 0.18);
  }

  /* Back side */
  .card--back {
    background: linear-gradient(135deg, var(--brand-blue-light) 0%, var(--brand-blue) 45%, var(--brand-blue-deep) 100%);
    display: flex;
    flex-direction: column;
    align-items: center;
    justify-content: center;
  }
  .card--back .wordmark {
    color: var(--card-white);
    font-weight: 300;
    font-size: 80px;
    letter-spacing: 2px;
    line-height: 1;
  }
  .card--back .web-line {
    margin-top: 24px;
    color: rgba(255, 255, 255, 0.85);
    font-size: 12px;
    letter-spacing: 9px;
  }

  /* Front side */
  .card--front {
    background: var(--card-white);
  }
  .tone-field {
    position: absolute;
    inset: 0;
    background: linear-gradient(100deg, rgba(255,255,255,0) 0%, rgba(255,255,255,0) 40%, var(--brand-blue-mist) 62%, var(--brand-blue-light) 84%, var(--brand-blue) 100%);
  }
  .holder {
    position: absolute;
    top: 30px;
    left: 48px;
  }
  .holder-name {
    color: var(--brand-blue);
    font-weight: 700;
    font-size: 17px;
    letter-spacing: 0.5px;
    line-height: 1.1;
  }
  .holder-title {
    color: var(--ink-grey);
    font-size: 12px;
    letter-spacing: 0.5px;
  }
  .card--front .wordmark {
    position: absolute;
    top: 80px;
    left: 44px;
    color: var(--brand-blue);
    font-weight: 300;
    font-size: 66px;
    letter-spacing: 2px;
    line-height: 1;
  }
  .contact {
    position: absolute;
    left: 48px;
    bottom: 38px;
    list-style: none;
  }
  .contact li {
    display: flex;
    align-items: center;
    gap: 9px;
    color: var(--ink-grey);
    font-size: 14px;
    line-height: 24px;
  }
  .contact svg {
    width: 14px;
    height: 14px;
    flex: none;
  }
</style>
</head>
<body>
<main class="sheet">
  <section class="card card--back" aria-label="Card back">
    <div class="wordmark">quilmora</div>
    <div class="web-line">www.quilmora.com</div>
  </section>

  <section class="card card--front" aria-label="Card front">
    <div class="tone-field" role="img" aria-label="Soft blue gradient where a faint decorative lettering pattern belongs"></div>

    <div class="holder">
      <div class="holder-name">DEVIN HOLT</div>
      <div class="holder-title">PRESIDENT</div>
    </div>

    <div class="wordmark">quilmora</div>

    <ul class="contact">
      <li>
        <svg viewBox="0 0 16 16" aria-hidden="true"><path fill="var(--brand-blue)" d="M3.6 1.2l2.4 2.6-1.3 1.8c.9 2 2.7 3.9 4.7 4.7l1.8-1.3 2.6 2.4-1.5 2.4C7 13.6 2.4 9 2.1 2.7z"/></svg>
        (800) 471-2960
      </li>
      <li>
        <svg viewBox="0 0 16 16" aria-hidden="true"><rect x="1" y="3" width="14" height="10" rx="1" fill="var(--brand-blue)"/><path d="M1.5 3.8L8 9l6.5-5.2" fill="none" stroke="#fff" stroke-width="1.2"/></svg>
        sleep@quilmora.com
      </li>
      <li>
        <svg viewBox="0 0 16 16" aria-hidden="true"><circle cx="8" cy="8" r="7" fill="var(--brand-blue)"/><path d="M1 8h14M8 1c-3 3.5-3 10.5 0 14M8 1c3 3.5 3 10.5 0 14" fill="none" stroke="#fff" stroke-width="1"/></svg>
        www.quilmora.com
      </li>
    </ul>
  </section>
</main>
</body>
</html>
```